Site for entrepreneurs/small businesses needs Logo, Homepage

Looking for a logo, either an icon, or stylized text, or a combination of both, and a home page design which fits with it. The logo will be for use on the public website as well as for printed collateral (business cards, post cards, brochures and various other marketing materials).

The site is called Orbitwell (Orbitwell.example). This is to be a national, and eventually an international brand. The new service will provide an easy-to-use platform for entrepreneurs to build their business and web presence together in an integrated way which allows them to focus on their core competency.

The site/service will be dead-simple to use, A/B/C, 1/2/3. We will want some sort of "Get started for FREE" promotional space to collect the person's email address with multiple points of interest which guide the user back to this one call to action: sign up for free. We will feature editorial/blog stories, customer testimonials, and present several key features the the reader just can't live without if they are starting a new business.

Criteria:
* Refer to our comparable sites/logos in the design document attached
* Incorporate our color scheme (but complementary colors welcome)
* No Serif fonts!
* No photo-realistic elements for logo
* Logo must present well in gray scale and/or black/white (for printed materials)
* Strokes/borders that are wider to promote simplicity (vs. thin/precise lines which promote technical complexity)

Inspirations:
* Creative/Custom (but legible) fonts
* Excitement, energetic, jumping for joy
* Karate / Ninja / Power / Precision
* Dance Moves
* Regional influences: California, Silicon Valley, West Coast, Surf City, Beaches, Sunset
* Simple/easy, no-brainer solutions

Target Market(s)

Small Businesses / Entrepreneurs

Logo Text

Orbitwell or Orbitwell.example

Number of Pages Required

1 page

Font styles to use
Sans Serif
Decorative

Requirements
Must have
• See the attached style guide (PDF)

```html
<!DOCTYPE html>
<html lang="en">
<head>
<meta charset="utf-8">
<title>Orbitwell – Entrepreneurs to build the business</title>
<link href="https://fonts.googleapis.com/css2?family=Roboto+Condensed:wght@400;700&family=Open+Sans:wght@400;600&display=swap" rel="stylesheet">
<style>
:root{
  --purple:#8a10c8;
  --purple-dark:#6a0aa0;
  --orange:#f7941d;
  --orange-deep:#f15a24;
  --grey-band:#f1f1f3;
  --ink:#555;
  --ink-dark:#333;
  --line:#d8d8d8;
  --white:#fff;
}
*{box-sizing:border-box;margin:0;padding:0}
html,body{width:1200px;height:2920px;overflow:hidden;background:var(--white)}
body{position:relative;font-family:"Open Sans",Arial,sans-serif;color:var(--ink)}
.abs{position:absolute}
.backdrop{position:absolute;left:0;top:0;width:1200px;height:2920px}
.heading{font-family:"Roboto Condensed",Arial,sans-serif;font-weight:700;text-transform:uppercase}
.btn{position:absolute;display:flex;align-items:center;justify-content:center;background:linear-gradient(90deg,var(--orange),var(--orange-deep));color:var(--white);font-family:"Roboto Condensed",Arial,sans-serif;font-weight:700;font-size:17px;border-radius:3px}
.btn.purple{background:linear-gradient(90deg,var(--purple),var(--purple-dark))}

/* header */
.brand{left:28px;top:22px;display:flex;align-items:center;gap:10px}
.brand-dot{width:40px;height:40px;border-radius:50%;background:var(--purple)}
.brand-name{font-family:"Roboto Condensed",Arial,sans-serif;font-weight:700;font-size:30px;color:var(--purple)}
.nav{left:515px;top:76px;display:flex;gap:34px;font-family:"Roboto Condensed",Arial,sans-serif;font-weight:700;font-size:17px;color:var(--white);text-transform:uppercase}

/* hero */
.hero-title{left:100px;top:226px;font-size:44px;color:var(--purple);letter-spacing:1px}
.hero-sub{left:100px;top:282px;font-family:"Roboto Condensed",Arial,sans-serif;font-weight:700;font-size:26px;color:var(--orange)}
.field{top:320px;height:46px;border:2px solid #cfcfcf;background:var(--white);padding:0 14px;display:flex;align-items:center;font-size:15px;color:#666}
.hero-art{left:648px;top:120px;width:370px;height:370px;border-radius:50%;border:10px solid var(--purple);background:linear-gradient(160deg,#fde7c4,#f6f0fb)}

/* blog */
.blog-art{left:58px;top:740px;width:400px;height:460px;border-radius:46% 54% 50% 50%/52% 46% 54% 48%;border:10px solid var(--orange);background:linear-gradient(160deg,#fff3dc,#fde0b4)}
.blog-head{right:112px;top:978px;font-size:40px;color:var(--purple);display:flex;align-items:center;gap:14px}
.blog-meta{right:112px;top:1036px;font-size:14px;color:var(--orange);display:flex;gap:22px}
.blog-text{right:112px;width:560px;text-align:right;font-size:14.5px;line-height:24px;color:var(--ink)}

/* features */
.section-title{left:0;width:1200px;text-align:center;font-size:42px;color:var(--purple)}
.rule{left:556px;width:88px;height:4px;background:var(--purple)}
.section-intro{left:160px;width:880px;text-align:center;font-size:15px;line-height:26px}
.feature{border-radius:50%;background:var(--white);box-shadow:0 6px 24px rgba(0,0,0,.14);display:flex;flex-direction:column;align-items:center;justify-content:center;text-align:center}
.feature-label{font-family:"Roboto Condensed",Arial,sans-serif;font-weight:700;font-size:22px;text-transform:uppercase;color:var(--purple);margin-top:12px}
.feature.focus{background:var(--purple);border:10px solid var(--white);box-shadow:0 0 0 6px var(--purple),0 8px 26px rgba(0,0,0,.2)}
.feature.focus .feature-label{color:var(--white);margin:0 0 10px}
.feature.focus p{color:var(--white);font-size:14px;line-height:22px;width:220px}

/* testimonials */
.quote-card{top:2170px;width:490px;height:220px;border:3px solid var(--purple);border-radius:10px;background:var(--white);padding:26px 168px 0 26px;font-size:14px;line-height:23px;text-align:center}
.quote-card .who{display:block;text-align:right;font-weight:600;margin-top:8px;color:var(--ink-dark)}
.quote-photo{top:20px;right:22px;width:126px;height:126px;border-radius:8px;background:linear-gradient(160deg,#d9cbbd,#8f7a6a)}
.quote-mark{bottom:-12px;left:218px;font-family:"Roboto Condensed",Arial,sans-serif;font-weight:700;font-size:96px;line-height:60px;color:var(--purple);height:60px;overflow:hidden}
.quote-tail{bottom:-24px;width:30px;height:30px;background:var(--white);border-right:3px solid var(--purple);border-bottom:3px solid var(--purple);transform:rotate(45deg)}

/* footer */
.footer-contact{right:70px;display:flex;align-items:center;gap:16px;font-size:14px;color:var(--ink-dark);text-align:right;line-height:22px}
.icon-ring{width:38px;height:38px;border-radius:50%;border:2px solid var(--purple);display:flex;align-items:center;justify-content:center}
.social{left:96px;top:2776px;display:flex;gap:10px}
.social span{width:32px;height:32px;border-radius:50%;border:2px solid #555}
.footer-rule{left:96px;top:2846px;width:1010px;height:1px;background:var(--line)}
.copyright{left:0;top:2866px;width:1200px;text-align:center;font-size:14px;font-weight:600;color:var(--ink-dark)}
</style>
</head>
<body>

<svg class="backdrop" viewBox="0 0 1200 2920" aria-hidden="true">
  <path d="M0 470 C260 560 420 520 560 560 C760 620 820 700 1200 640 L1200 1940 C900 1990 640 1900 380 1950 C220 1980 80 1930 0 1960 Z" fill="var(--grey-band)"/>
  <path d="M400 0 L1200 0 L1200 430 C1140 400 1080 300 980 260 C880 220 780 250 700 190 C600 120 560 40 400 0 Z" fill="var(--purple)"/>
  <path d="M0 2420 C300 2470 500 2400 760 2450 C980 2490 1100 2460 1200 2440 L1200 2920 L0 2920 Z" fill="#fafafa"/>
</svg>

<header>
  <div class="abs brand"><span class="brand-dot"></span><span class="brand-name">Orbitwell</span></div>
  <a class="btn" style="left:900px;top:22px;width:282px;height:40px;font-size:15px">GET STARTED FOR FREE</a>
  <nav class="abs nav"><span>Home</span><span>About</span><span>Features</span><span>Blog</span><span>Testimonials</span><span>Contact Us</span></nav>
</header>

<section class="hero">
  <h1 class="abs heading hero-title">Orbitwell</h1>
  <p class="abs hero-sub">Entrepreneurs to build the business</p>
  <div class="abs field" style="left:100px;width:220px">User Name</div>
  <div class="abs field" style="left:332px;width:224px">Email Id</div>
  <a class="btn purple" style="left:100px;top:368px;width:142px;height:46px">Sign Up For Free</a>
  <div class="abs hero-art" role="img" aria-label="Illustration of two happy entrepreneurs celebrating with business icons around them"></div>
</section>

<section class="blog">
  <div class="abs blog-art" role="img" aria-label="Illustration of two business people with idea and growth icons"></div>
  <h2 class="abs heading blog-head">
    <svg width="36" height="28" viewBox="0 0 36 28" aria-hidden="true"><path d="M12 4 L3 14 L12 24 M24 4 L33 14 L24 24" fill="none" stroke="var(--purple)" stroke-width="4" stroke-linecap="round"/></svg>
    Our Blog Stories
  </h2>
  <div class="abs blog-meta"><span>May 6, 2018</span><span>12 Comments</span></div>
  <p class="abs blog-text" style="top:1070px">Our team shares simple playbooks for new founders, from naming your idea to landing the first paying customer, so you can spend more time doing the work you love most.</p>
  <p class="abs blog-text" style="top:1150px;width:540px">Each story is short, practical and tested by real small business owners. Read a new guide every week and put one clear step into action before Friday arrives.</p>
  <a class="btn" style="left:990px;top:1196px;width:100px;height:46px;font-size:15px">Read More</a>
</section>

<section class="features">
  <h2 class="abs heading section-title" style="top:1342px">Key Features</h2>
  <div class="abs rule" style="top:1398px"></div>
  <p class="abs section-intro" style="top:1420px">Everything you need to launch, sell and grow sits in one place. Pick a tool, follow the steps and watch your business and website come together.</p>

  <svg class="abs" style="left:30px;top:1630px" width="30" height="50" viewBox="0 0 30 50" aria-hidden="true"><path d="M24 4 L6 25 L24 46" fill="none" stroke="#777" stroke-width="4"/></svg>
  <svg class="abs" style="left:1140px;top:1630px" width="30" height="50" viewBox="0 0 30 50" aria-hidden="true"><path d="M6 4 L24 25 L6 46" fill="none" stroke="#777" stroke-width="4"/></svg>

  <div class="abs feature" style="left:140px;top:1540px;width:240px;height:240px">
    <svg width="62" height="62" viewBox="0 0 62 62" aria-hidden="true"><rect x="10" y="6" width="36" height="48" rx="3" fill="none" stroke="var(--purple)" stroke-width="4"/><path d="M18 20h20M18 30h20M18 40h12" stroke="var(--orange)" stroke-width="4"/></svg>
    <span class="feature-label">Business</span>
  </div>
  <div class="abs feature focus" style="left:446px;top:1500px;width:310px;height:310px">
    <span class="feature-label">Entrepreneurs</span>
    <p>Plan, register and launch your venture with guided checklists built for first-time founders.</p>
  </div>
  <div class="abs feature" style="left:820px;top:1540px;width:240px;height:240px">
    <svg width="62" height="62" viewBox="0 0 62 62" aria-hidden="true"><path d="M16 44 V30 a15 15 0 0 1 30 0 V44 Z" fill="none" stroke="var(--orange-deep)" stroke-width="4"/><path d="M10 50h42" stroke="var(--purple)" stroke-width="4"/><path d="M31 6v6M12 14l4 4M50 14l-4 4" stroke="var(--orange-deep)" stroke-width="4"/></svg>
    <span class="feature-label">Notification</span>
  </div>
  <a class="btn" style="left:520px;top:1852px;width:160px;height:46px;font-size:15px">More Features</a>
</section>

<section class="testimonials">
  <h2 class="abs heading section-title" style="top:2032px">Our Testimonials</h2>
  <div class="abs rule" style="top:2088px"></div>

  <svg class="abs" style="left:30px;top:2258px" width="30" height="50" viewBox="0 0 30 50" aria-hidden="true"><path d="M24 4 L6 25 L24 46" fill="none" stroke="#777" stroke-width="4"/></svg>
  <svg class="abs" style="left:1140px;top:2258px" width="30" height="50" viewBox="0 0 30 50" aria-hidden="true"><path d="M6 4 L24 25 L6 46" fill="none" stroke="#777" stroke-width="4"/></svg>

  <article class="abs quote-card" style="left:100px">
    <div class="abs quote-tail" style="left:90px"></div>
    <p>Orbitwell helped me open my shop online in a weekend. The steps were clear and nothing felt technical.</p>
    <span class="who">- Rowan Pell</span>
    <div class="abs quote-photo" role="img" aria-label="Portrait photo of customer Rowan Pell"></div>
    <div class="abs quote-mark">&rdquo;</div>
  </article>
  <article class="abs quote-card" style="left:612px">
    <div class="abs quote-tail" style="left:90px"></div>
    <p>I finally have one place for my site, my invoices and my leads. Signing up took two minutes.</p>
    <span class="who">- Tessa Marlow</span>
    <div class="abs quote-photo" role="img" aria-label="Portrait photo of customer Tessa Marlow"></div>
    <div class="abs quote-mark">&rdquo;</div>
  </article>
</section>

<footer>
  <div class="abs brand" style="left:auto;right:70px;top:2560px;gap:12px"><span class="brand-dot" style="width:48px;height:48px"></span><span class="brand-name" style="font-size:36px">Orbitwell</span></div>
  <div class="abs footer-contact" style="top:2704px">
    <div><strong>Orbitwell</strong><br>48 Harbour Lane, Westfield, CA 90210</div>
    <span class="icon-ring"><svg width="18" height="22" viewBox="0 0 18 22" aria-hidden="true"><path d="M9 21 C3 13 2 10 2 8 a7 7 0 0 1 14 0 c0 2-1 5-7 13Z" fill="none" stroke="var(--purple)" stroke-width="2.5"/><circle cx="9" cy="8" r="2.5" fill="var(--purple)"/></svg></span>
  </div>
  <div class="abs footer-contact" style="top:2770px">
    <div>555 0142 778</div>
    <span class="icon-ring"><svg width="18" height="18" viewBox="0 0 18 18" aria-hidden="true"><path d="M4 1 L7 5 L5 7 C6 10 8 12 11 13 L13 11 L17 14 L15 17 C8 17 1 10 1 3 Z" fill="var(--purple)"/></svg></span>
  </div>
  <div class="abs social" aria-label="Social links"><span></span><span></span><span></span><span></span><span></span><span></span><span></span></div>
  <div class="abs footer-rule"></div>
  <p class="abs copyright">Copyrights © 2018 Orbitwell. All Rights Reserved.</p>
</footer>

</body>
</html>
```